BrivoNest Learning App for Children with Dyslexia

Project Description:

We are seeking a talented UI/UX designer to create engaging and intuitive designs for Brivonest, an innovative educational app designed to help children learn letters and words through a multisensory learning approach. The app aims to be particularly helpful for children with dyslexia, providing a supportive and interactive learning environment.

Key App Features & Design Requirements:

Account Creation Screen: Design a welcoming and straightforward sign-up page that allows users to register with their email or continue with Quarnix. The design should be clean, focusing on user-friendliness and accessibility, adhering to our terms of service and privacy policy.

Main Screen Design: The main screen should allocate at least 4/6 of its height to the interactive drawing area. It needs to display word prompts in both correct and scrambled orders and include options to "Show all Words," "Play all words," and a search function. The interface should be vibrant, engaging, and easy to navigate for children.

Profile Section: Create a user-friendly profile page that allows users to edit their profile image, name, username, email, links, and bio. The design should be clean and encourage user engagement.

BrivoTally Page: This section will display the user's learning progress, including rankings, a learning curve, and recently learned words. It should visually represent progress in a motivating and understandable way, suitable for a younger audience.

Visual and Auditory Feedback Implementation: Incorporate elements that support visual and auditory feedback, using dyslexia-friendly formats. This includes choosing appropriate colors, fonts, and auditory cues.

Accessibility and Customization Settings: Designs should include settings for adjusting visual contrast, font size, and the word list to accommodate individual preferences and needs.

Feel free to add more interactions and/or pages.

Design preferences:

Color Scheme: Use a bright, inviting color palette that stimulates learning and engagement without overwhelming the users.
Font Selection: Opt for fonts that are readable and accessible, particularly for users with dyslexia.
Icons and Graphics: Design custom icons and graphics that are cohesive with the app's theme and purpose. Illustrations should be simple, relatable, and supportive of the learning process.

Target Market(s)

Educational

Industry/Entity Type

Educational

Colors
0054AA
0677BA
7BADD7
CADEEF
E8F1F8
0094D4
00A9DD
6FCCEA
C7EBF8
E9F6FB

Requirements
Must have
• Educational app, a writing area, scoring and account management
Nice to have
• Statistics, Ranking Page, Settings and some nice visual features

```html
<!DOCTYPE html>
<html lang="en">
<head>
<meta charset="utf-8">
<title>Brivonest – App Screens</title>
<link rel="stylesheet" href="https://fonts.googleapis.com/css2?family=Lexend:wght@300;400;500;600&display=swap">
<style>
  :root{
    --navy:#0054AA;
    --ocean:#0677BA;
    --sky:#0094D4;
    --cyan:#00A9DD;
    --mist:#C7EBF8;
    --ice:#E9F6FB;
    --grey-btn:#D3D7DC;
    --ink:#1d2530;
    --muted:#6a7380;
    --line:#e1e5ea;
    --stage:#0a65b7;
  }
  *{box-sizing:border-box;margin:0;padding:0}
  html,body{width:1200px;height:839px;overflow:hidden}
  body{background:var(--stage);font-family:"Lexend",sans-serif;position:relative;color:var(--ink)}
  .screen{position:absolute;width:285px;height:617px;border-radius:30px;overflow:hidden;background:#fff}
  .screen--signup{left:88px;top:85px}
  .screen--main{left:457px;top:131px}
  .screen--profile{left:827px;top:85px}
  .abs{position:absolute}
  .status{position:absolute;top:0;left:0;right:0;height:30px;color:#fff;font-size:12px;font-weight:500}
  .status__time{position:absolute;left:15px;top:9px}
  .status__icons{position:absolute;right:14px;top:10px}
  .header{position:absolute;left:0;top:0;right:0;background:var(--navy);color:#fff}
  .panel{position:absolute;left:0;right:0;background:#fff;border-radius:18px 18px 0 0}
  .deco{position:absolute;inset:0;pointer-events:none}
  .center{left:0;right:0;text-align:center}

  /* sign-up */
  .brand{top:60px;font-size:23px;font-weight:500;letter-spacing:-.2px}
  .tagline{top:89px;font-size:13px;font-weight:400}
  .signup__title{top:178px;font-size:13px;font-weight:500}
  .signup__lead{top:199px;font-size:11px;font-weight:300;color:#333}
  .field{left:30px;width:224px;top:227px;height:35px;border:2px solid var(--line);border-radius:4px;font-size:10.5px;color:#9aa2ad;padding:9px 12px;font-weight:300}
  .btn{position:absolute;left:30px;width:224px;height:33px;border-radius:3px;color:#fff;font-size:11.5px;font-weight:500;display:flex;align-items:center;justify-content:center;gap:6px}
  .btn--navy{top:273px;background:var(--navy)}
  .btn--cyan{top:349px;background:var(--cyan)}
  .brand-dot{width:16px;height:16px;border-radius:50%;background:#fff}
  .divider{left:30px;width:224px;top:321px;display:flex;align-items:center;gap:6px;font-size:7px;color:#555}
  .divider::before,.divider::after{content:"";flex:1;height:1px;background:#cfd4da}
  .legal{top:396px;font-size:11px;font-weight:300;color:var(--muted);line-height:17px}
  .legal a{color:var(--navy);text-decoration:none;font-weight:400}

  /* nav */
  .nav{position:absolute;left:0;right:0;bottom:0;height:51px;background:var(--navy);border-radius:14px 14px 0 0;display:flex;justify-content:space-around;padding:0 4px}
  .nav__item{width:66px;display:flex;flex-direction:column;align-items:center;color:#fff;font-size:10.5px;font-weight:300;padding-top:14px;gap:3px}
  .nav__item svg{width:15px;height:15px;fill:none;stroke:#fff;stroke-width:1.4}

  /* main */
  .icon-btn{position:absolute;left:14px;top:43px;width:26px;height:26px;border-radius:50%;background:var(--cyan);display:flex;align-items:center;justify-content:center}
  .screen-title{top:46px;font-size:15px;font-weight:500;color:#fff}
  .points{right:14px;top:52px;font-size:10px;font-weight:500;color:#fff}
  .draw-area{left:0;right:0;top:82px;height:210px;background:var(--ice);border-radius:16px 16px 0 0}
  .pen{left:119px;top:165px;width:44px;height:44px;border-radius:50%;background:var(--navy);border:3px solid #7BADD7;display:flex;align-items:center;justify-content:center}
  .action{position:absolute;top:305px;height:28px;width:107px;border-radius:3px;color:#fff;font-size:11px;font-weight:500;display:flex;align-items:center;justify-content:center}
  .action--muted{left:30px;background:var(--grey-btn)}
  .action--play{left:150px;background:var(--cyan)}
  .word{position:absolute;width:72px;height:27px;border-radius:14px;background:#fff;box-shadow:0 2px 7px rgba(0,84,170,.12);color:var(--navy);font-size:11.5px;font-weight:400;display:flex;align-items:center;justify-content:center}
  .results{left:27px;width:229px;top:434px;height:35px;border:2px solid var(--line);border-radius:18px;color:var(--navy);font-size:11.5px;font-weight:500;display:flex;align-items:center;justify-content:center;letter-spacing:.2px}

  /* profile */
  .avatar{left:111px;top:102px;width:62px;height:62px;border-radius:50%;background:radial-gradient(circle at 50% 40%,#c9a58f 0%,#6b4a3c 55%,#2b2a33 100%)}
  .avatar-add{left:155px;top:147px;width:16px;height:16px;border-radius:50%;background:var(--navy);border:2px solid #fff;color:#fff;font-size:11px;line-height:11px;text-align:center}
  .edit-photo{top:170px;font-size:11.5px;font-weight:500;color:var(--navy)}
  .row-label{position:absolute;left:16px;width:78px;height:25px;background:var(--navy);color:#fff;font-size:11px;border-radius:12px 0 0 12px;padding:5px 0 0 11px;font-weight:400}
  .row-value{position:absolute;left:106px;font-size:11px;font-weight:300;color:#333}
  .row-go{position:absolute;left:252px;width:16px;height:16px;border-radius:50%;background:var(--cyan);display:flex;align-items:center;justify-content:center}
  .add-link{color:var(--cyan)!important;font-weight:400!important}
</style>
</head>
<body>

<!-- Sign-up screen -->
<section class="screen screen--signup">
  <div class="header" style="height:160px"></div>
  <div class="status"><span class="status__time">9:41</span>
    <svg class="status__icons" width="46" height="10" viewBox="0 0 46 10"><g fill="#fff"><rect x="0" y="7" width="2" height="3"/><rect x="3" y="5" width="2" height="5"/><rect x="6" y="3" width="2" height="7"/><rect x="9" y="1" width="2" height="9"/><path d="M16 4a7 7 0 0 1 10 0l-1 1a5.5 5.5 0 0 0-8 0zM18 6a4 4 0 0 1 6 0l-3 3z"/><rect x="31" y="1" width="13" height="8" rx="2"/><rect x="44.5" y="3.5" width="1.5" height="3"/></g></svg>
  </div>
  <div class="abs center brand">Brivonest</div>
  <div class="abs center tagline">Learn letters and words</div>
  <div class="panel" style="top:146px;bottom:0"></div>
  <svg class="deco" viewBox="0 0 285 617">
    <circle cx="270" cy="128" r="24" fill="none" stroke="#00A9DD" stroke-width="2.5"/>
    <rect x="230" y="100" width="60" height="46" fill="#0054AA"/>
    <circle cx="0" cy="199" r="11" fill="#00A9DD"/>
    <circle cx="-14" cy="494" r="46" fill="none" stroke="#00A9DD" stroke-width="2.5"/>
  </svg>
  <div class="abs center signup__title">Create an account</div>
  <div class="abs center signup__lead">Enter your email to sign up for this app</div>
  <div class="abs field">email@domain.com</div>
  <div class="btn btn--navy">Sign up with email</div>
  <div class="abs divider">or continue with</div>
  <div class="btn btn--cyan"><span class="brand-dot"></span>Quarnix</div>
  <p class="abs center legal">By clicking continue, you agree to our<br><a href="#">Terms of Service</a> and <a href="#">Privacy Policy</a></p>
  <nav class="nav">
    <div class="nav__item"><svg viewBox="0 0 16 16"><path d="M2 7.5 8 2.5l6 5V14H2z"/></svg>Home</div>
    <div class="nav__item"><svg viewBox="0 0 16 16"><path d="M4 11V7a4 4 0 0 1 8 0v4l1.5 1.5h-11zM6.5 14h3M8 1.5v1"/></svg>Notification</div>
    <div class="nav__item"><svg viewBox="0 0 16 16"><path d="M8 14 2.5 8.5A3.2 3.2 0 0 1 8 4a3.2 3.2 0 0 1 5.5 4.5z"/></svg>Heart</div>
    <div class="nav__item"><svg viewBox="0 0 16 16"><circle cx="8" cy="5" r="3"/><path d="M2.5 14.5a5.5 5.5 0 0 1 11 0"/></svg>Profile</div>
  </nav>
</section>

<!-- Main screen -->
<section class="screen screen--main">
  <div class="header" style="height:100px"></div>
  <div class="status"><span class="status__time">9:41</span>
    <svg class="status__icons" width="46" height="10" viewBox="0 0 46 10"><g fill="#fff"><rect x="0" y="7" width="2" height="3"/><rect x="3" y="5" width="2" height="5"/><rect x="6" y="3" width="2" height="7"/><rect x="9" y="1" width="2" height="9"/><path d="M16 4a7 7 0 0 1 10 0l-1 1a5.5 5.5 0 0 0-8 0zM18 6a4 4 0 0 1 6 0l-3 3z"/><rect x="31" y="1" width="13" height="8" rx="2"/><rect x="44.5" y="3.5" width="1.5" height="3"/></g></svg>
  </div>
  <div class="icon-btn"><svg width="12" height="10" viewBox="0 0 12 10"><g stroke="#fff" stroke-width="1.8" stroke-linecap="round"><path d="M1 1h10M1 5h10M1 9h10"/></g></svg></div>
  <div class="abs center screen-title">Main Screen</div>
  <div class="abs points">16 Points</div>
  <div class="abs draw-area"></div>
  <div class="abs pen"><svg width="18" height="18" viewBox="0 0 18 18"><path d="M4 13 12 5l2 2-8 8H4z" fill="#fff"/><path d="M12.5 4.5 14 3l2 2-1.5 1.5z" fill="#fff"/><path d="M2 16.5h9" stroke="#fff" stroke-width="1.3" stroke-linecap="round"/></svg></div>
  <div class="panel" style="top:280px;bottom:0"></div>
  <svg class="deco" viewBox="0 0 285 617">
    <circle cx="0" cy="501" r="11" fill="#00A9DD"/>
    <polygon points="285,471 285,547 243,508" fill="#C7EBF8" role="img" aria-label="Dotted accent pattern"/>
  </svg>
  <div class="action action--muted">Show All Words</div>
  <div class="action action--play">Play all words</div>
  <div class="word" style="left:29px;top:353px">One</div>
  <div class="word" style="left:107px;top:353px">Two</div>
  <div class="word" style="left:185px;top:353px">Three</div>
  <div class="word" style="left:29px;top:391px">Four</div>
  <div class="word" style="left:107px;top:391px">Five</div>
  <div class="word" style="left:185px;top:391px">Six</div>
  <div class="abs results">SHOW ME THE RESULTS</div>
  <nav class="nav">
    <div class="nav__item"><svg viewBox="0 0 16 16"><path d="M2 7.5 8 2.5l6 5V14H2z"/></svg>Home</div>
    <div class="nav__item"><svg viewBox="0 0 16 16"><path d="M4 11V7a4 4 0 0 1 8 0v4l1.5 1.5h-11zM6.5 14h3M8 1.5v1"/></svg>Notification</div>
    <div class="nav__item"><svg viewBox="0 0 16 16"><path d="M8 14 2.5 8.5A3.2 3.2 0 0 1 8 4a3.2 3.2 0 0 1 5.5 4.5z"/></svg>Heart</div>
    <div class="nav__item"><svg viewBox="0 0 16 16"><circle cx="8" cy="5" r="3"/><path d="M2.5 14.5a5.5 5.5 0 0 1 11 0"/></svg>Profile</div>
  </nav>
</section>

<!-- Profile screen -->
<section class="screen screen--profile">
  <div class="header" style="height:100px"></div>
  <div class="status"><span class="status__time">9:41</span>
    <svg class="status__icons" width="46" height="10" viewBox="0 0 46 10"><g fill="#fff"><rect x="0" y="7" width="2" height="3"/><rect x="3" y="5" width="2" height="5"/><rect x="6" y="3" width="2" height="7"/><rect x="9" y="1" width="2" height="9"/><path d="M16 4a7 7 0 0 1 10 0l-1 1a5.5 5.5 0 0 0-8 0zM18 6a4 4 0 0 1 6 0l-3 3z"/><rect x="31" y="1" width="13" height="8" rx="2"/><rect x="44.5" y="3.5" width="1.5" height="3"/></g></svg>
  </div>
  <div class="icon-btn"><svg width="8" height="10" viewBox="0 0 8 10"><path d="M6 1 2 5l4 4" fill="none" stroke="#fff" stroke-width="1.6" stroke-linecap="round"/></svg></div>
  <div class="abs center screen-title">Profile</div>
  <div class="panel" style="top:82px;bottom:0;border-radius:0"></div>
  <svg class="deco" viewBox="0 0 285 617">
    <circle cx="245" cy="82" r="5" fill="#00A9DD"/>
    <polygon points="0,82 63,82 26,120 0,104" fill="#C7EBF8" role="img" aria-label="Dotted accent pattern"/>
    <circle cx="0" cy="518" r="25" fill="none" stroke="#00A9DD" stroke-width="2.5"/>
  </svg>
  <div class="abs avatar" role="img" aria-label="User profile photo"></div>
  <div class="abs avatar-add">+</div>
  <div class="abs center edit-photo">Edit profile image</div>

  <div class="row-label" style="top:207px">Name</div>
  <div class="row-value" style="top:212px">Mara Quill</div>
  <div class="row-go" style="top:211px"><svg width="6" height="8" viewBox="0 0 6 8"><path d="M1.5 1 4.5 4l-3 3" fill="none" stroke="#fff" stroke-width="1.4"/></svg></div>

  <div class="row-label" style="top:245px">Username</div>
  <div class="row-value" style="top:250px">@username</div>
  <div class="row-go" style="top:249px"><svg width="6" height="8" viewBox="0 0 6 8"><path d="M1.5 1 4.5 4l-3 3" fill="none" stroke="#fff" stroke-width="1.4"/></svg></div>

  <div class="row-label" style="top:283px">Email</div>
  <div class="row-value" style="top:288px">name@domain.com</div>
  <div class="row-go" style="top:287px"><svg width="6" height="8" viewBox="0 0 6 8"><path d="M1.5 1 4.5 4l-3 3" fill="none" stroke="#fff" stroke-width="1.4"/></svg></div>

  <div class="row-label" style="top:321px">Links</div>
  <div class="row-value" style="top:326px">website.net</div>
  <div class="row-value" style="top:349px">mylink.net</div>
  <div class="row-value" style="top:372px">yourlink.net</div>
  <div class="row-value add-link" style="top:395px">+ Add link</div>
  <div class="row-go" style="top:325px"><svg width="6" height="8" viewBox="0 0 6 8"><path d="M1.5 1 4.5 4l-3 3" fill="none" stroke="#fff" stroke-width="1.4"/></svg></div>

  <div class="row-label" style="top:428px">Bio</div>
  <div class="row-value" style="top:433px">A description of this user.</div>
  <div class="row-go" style="top:432px"><svg width="6" height="8" viewBox="0 0 6 8"><path d="M1.5 1 4.5 4l-3 3" fill="none" stroke="#fff" stroke-width="1.4"/></svg></div>

  <nav class="nav">
    <div class="nav__item"><svg viewBox="0 0 16 16"><path d="M2 7.5 8 2.5l6 5V14H2z"/></svg>Home</div>
    <div class="nav__item"><svg viewBox="0 0 16 16"><path d="M4 11V7a4 4 0 0 1 8 0v4l1.5 1.5h-11zM6.5 14h3M8 1.5v1"/></svg>Notification</div>
    <div class="nav__item"><svg viewBox="0 0 16 16"><path d="M8 14 2.5 8.5A3.2 3.2 0 0 1 8 4a3.2 3.2 0 0 1 5.5 4.5z"/></svg>Heart</div>
    <div class="nav__item"><svg viewBox="0 0 16 16"><circle cx="8" cy="5" r="3"/><path d="M2.5 14.5a5.5 5.5 0 0 1 11 0"/></svg>Profile</div>
  </nav>
</section>

</body>
</html>
```